Harbor Lending Circle - business cards

we need new business cards for my company.
i've been in business for 25 years.
my wife and I are mortgage brokers.

we just bought the domain for a website with www.keysinhandhomes.example
that could be used in the design also.

On the business card would be
Front card:

Dale Whitmore
Owner/Loan Officer
Cell: (555) 417-2936
Harbor Lending Circle
4273 Pinecrest Lane
Larkspur Vale, ST 90000
Office (555) 309-6714
Fax (555) 309-6752
website www.keysinhandhomes.example

Back of Card:

HLC BRE #0587219 NMLS #864920
Dale Whitmore BRE # 01795564 NMLS #864137

```html
<!DOCTYPE html>
<html lang="en">
<head>
<meta charset="utf-8">
<title>Harbor Lending Circle – Business Cards</title>
<link rel="stylesheet" href="https://fonts.googleapis.com/css2?family=Open+Sans:wght@400;600;700&display=swap">
<style>
  :root {
    --maroon: #6b1a1d;
    --maroon-text: #7a1e22;
    --blush: #e3b7b5;
    --ink: #2b2b2b;
    --ink-soft: #555555;
    --paper: #ffffff;
    --backdrop: #e6e6e6;
    --rule: #7d7d7d;
  }
  * { box-sizing: border-box; margin: 0; padding: 0; }
  html, body {
    width: 1200px; height: 1200px; overflow: hidden;
    background: var(--backdrop);
    font-family: "Open Sans", sans-serif;
  }
  .canvas { position: relative; width: 1200px; height: 1200px; }
  .card {
    position: absolute; left: 250px; width: 700px; height: 400px;
    box-shadow: 0 6px 20px rgba(0,0,0,0.12);
  }
  .card--back { top: 160px; background: var(--maroon); color: var(--paper); }
  .card--front { top: 640px; background: var(--paper); color: var(--ink); }

  /* Back side */
  .back-brand {
    position: absolute; left: 210px; top: 120px;
    display: flex; align-items: center; gap: 16px;
  }
  .brand-mark { width: 30px; height: 30px; flex: none; }
  .back-brand .brand-mark { background: var(--paper); }
  .brand-name { font-weight: 700; font-size: 32px; line-height: 1.05; }
  .back-brand .brand-name { color: var(--paper); }
  .licenses {
    position: absolute; left: 256px; top: 218px;
    font-size: 17px; line-height: 1.45; color: var(--blush);
    list-style: none;
  }

  /* Front side */
  .front-brand {
    position: absolute; left: 56px; top: 150px; width: 260px;
    display: flex; align-items: center; gap: 12px;
  }
  .front-brand .brand-mark { background: var(--maroon-text); width: 24px; height: 24px; }
  .front-brand .brand-name { color: var(--maroon-text); font-size: 26px; }
  .divider {
    position: absolute; left: 330px; top: 90px; width: 1.5px; height: 220px;
    background: var(--rule);
  }
  .contact { position: absolute; left: 356px; top: 74px; font-size: 17px; line-height: 1.35; }
  .contact-name { font-weight: 700; font-size: 22px; color: var(--ink); }
  .contact-title { color: var(--ink-soft); margin-bottom: 2px; }
  .contact-list { list-style: none; }
  .contact-row { display: flex; align-items: flex-start; gap: 8px; color: var(--ink-soft); }
  .contact-row + .contact-row { margin-top: 2px; }
  .contact-row.gap-before { margin-top: 14px; }
  .icon { width: 16px; height: 16px; flex: none; margin-top: 3px; }
  .icon rect { fill: var(--maroon-text); }
  .icon .glyph { fill: var(--paper); stroke: none; }
  .icon .stroke { fill: none; stroke: var(--paper); stroke-width: 1.4; }
</style>
</head>
<body>
<main class="canvas">

  <section class="card card--back" aria-label="Card back">
    <div class="back-brand">
      <span class="brand-mark"></span>
      <span class="brand-name">Harbor Lending<br>Circle</span>
    </div>
    <ul class="licenses">
      <li>HLC BRE #0587219</li>
      <li>NMLS #864920</li>
      <li>Dale Whitmore BRE # 01795564</li>
      <li>NMLS #864137</li>
    </ul>
  </section>

  <section class="card card--front" aria-label="Card front">
    <div class="front-brand">
      <span class="brand-mark"></span>
      <span class="brand-name">Harbor Lending<br>Circle</span>
    </div>
    <div class="divider"></div>
    <div class="contact">
      <div class="contact-name">Dale Whitmore</div>
      <div class="contact-title">Owner/Loan Officer</div>
      <ul class="contact-list">
        <li class="contact-row">
          <svg class="icon" viewBox="0 0 16 16" aria-label="Cell"><rect width="16" height="16" rx="3"/><rect x="5" y="3" width="6" height="10" rx="1" style="fill:#fff"/></svg>
          <span>(555) 417-2936</span>
        </li>
        <li class="contact-row gap-before">
          <svg class="icon" viewBox="0 0 16 16" aria-label="Address"><rect width="16" height="16" rx="8"/><path class="glyph" d="M8 3.5 L13 8 H11.5 V12.5 H4.5 V8 H3 Z"/></svg>
          <span>4273 Pinecrest Lane<br>Larkspur Vale, ST 90000</span>
        </li>
        <li class="contact-row gap-before">
          <svg class="icon" viewBox="0 0 16 16" aria-label="Office"><rect width="16" height="16" rx="3"/><path class="stroke" d="M4.5 4 C4.5 9 7 11.5 12 11.5 L12 9.5 L10 9 L9 10 C7.5 9.3 6.7 8.5 6 7 L7 6 L6.5 4 Z"/></svg>
          <span>(555) 309-6714</span>
        </li>
        <li class="contact-row">
          <svg class="icon" viewBox="0 0 16 16" aria-label="Fax"><rect width="16" height="16" rx="3"/><rect class="stroke" x="4" y="6.5" width="8" height="5"/><path class="stroke" d="M5.5 6.5 V3.5 H10.5 V6.5"/></svg>
          <span>(555) 309-6752</span>
        </li>
        <li class="contact-row">
          <svg class="icon" viewBox="0 0 16 16" aria-label="Website"><rect width="16" height="16" rx="3"/><circle class="stroke" cx="8" cy="8" r="4.5"/><path class="stroke" d="M3.5 8 H12.5 M8 3.5 C6 6 6 10 8 12.5 C10 10 10 6 8 3.5"/></svg>
          <span>www.keysinhandhomes.example</span>
        </li>
      </ul>
    </div>
  </section>

</main>
</body>
</html>
```